BOLD & MINIMALIST DESIGN NEEDED

We want a very bold but minimalistic business card design that is impactful and utilizes both sides of the business card. Our current logo is included for your use.

We want bold fonts and good use of negative space. We don't want the logo to overpower the design.

Target Market(s)

Professionals who are building new commercial buildings.

Industry/Entity Type

Construction

Contact Information for Business Card

Name, Title, email, office phone, cell phone, website

Font styles to use
Serif
Sans Serif

Requirements
Must have
• Bold design!

```html
<!DOCTYPE html>
<html lang="en">
<head>
<meta charset="utf-8">
<title>Ridgecrest Build – Business Card</title>
<link rel="stylesheet" href="https://fonts.googleapis.com/css2?family=Lato:wght@400;700;900&display=swap">
<style>
  :root {
    --bg: #2e2e2e;
    --green-light: #8cc63f;
    --green: #5e9a1f;
    --green-deep: #2f5510;
    --ink: #161616;
    --paper: #ffffff;
    --text-dark: #2a2a2a;
  }
  * { margin: 0; padding: 0; box-sizing: border-box; }
  html, body { width: 1200px; height: 800px; overflow: hidden; }
  body {
    background: var(--bg);
    font-family: "Lato", sans-serif;
    display: flex;
    flex-direction: column;
    align-items: center;
    justify-content: center;
    gap: 40px;
  }
  .card {
    position: relative;
    width: 600px;
    height: 343px;
    border-radius: 16px;
    overflow: hidden;
  }

  /* Front side */
  .card--front {
    background: radial-gradient(circle at 35% 30%, var(--green) 0%, #4a7a18 45%, var(--green-deep) 100%);
  }
  .front-brand {
    position: absolute;
    left: 44px;
    top: 152px;
    display: flex;
    align-items: center;
    gap: 10px;
    color: var(--paper);
    font-weight: 900;
    font-size: 28px;
    letter-spacing: 0.5px;
    text-transform: uppercase;
    white-space: nowrap;
  }
  .front-decoration {
    position: absolute;
    right: 0;
    top: 0;
    width: 210px;
    height: 100%;
    background: linear-gradient(135deg, #9fd455 0%, var(--green-light) 35%, #1b1b1b 70%, #0d0d0d 100%);
    opacity: 0.9;
  }
  .brand-square {
    width: 16px;
    height: 16px;
    background: currentColor;
    flex: none;
  }

  /* Back side */
  .card--back { background: var(--paper); }
  .back-wave { position: absolute; inset: 0; }
  .holder {
    position: absolute;
    right: 40px;
    top: 40px;
    text-align: right;
  }
  .holder-name {
    color: var(--green);
    font-weight: 900;
    font-size: 30px;
    line-height: 1.1;
  }
  .holder-title {
    color: var(--text-dark);
    font-size: 15px;
    margin-top: 2px;
  }
  .name-tab {
    position: absolute;
    right: 0;
    top: 38px;
    width: 22px;
    height: 40px;
    background: var(--green-light);
  }
  .back-brand {
    position: absolute;
    left: 40px;
    top: 128px;
    display: flex;
    align-items: center;
    gap: 10px;
    color: var(--ink);
    font-weight: 900;
    font-size: 26px;
    text-transform: uppercase;
    white-space: nowrap;
  }
  .back-brand .brand-square { background: var(--green-light); }
  .contact-list {
    position: absolute;
    left: 40px;
    bottom: 18px;
    list-style: none;
    color: var(--paper);
    font-size: 15px;
    line-height: 1.45;
  }
  .contact-list li, .web-line { display: flex; align-items: center; gap: 8px; }
  .contact-list svg, .web-line svg { width: 14px; height: 14px; fill: none; stroke: var(--paper); stroke-width: 2; }
  .office {
    position: absolute;
    right: 36px;
    top: 176px;
    text-align: right;
    color: var(--paper);
    font-size: 15px;
    line-height: 1.35;
  }
  .web-line { justify-content: flex-end; margin-top: 10px; }
</style>
</head>
<body>

<section class="card card--front" aria-label="Card front">
  <div class="front-brand"><span class="brand-square"></span>Ridgecrest Build</div>
  <div class="front-decoration" role="img" aria-label="Large brand monogram decoration in green and black"></div>
</section>

<section class="card card--back" aria-label="Card back">
  <svg class="back-wave" viewBox="0 0 600 343" preserveAspectRatio="none" aria-hidden="true">
    <defs>
      <linearGradient id="waveGreen" x1="0" y1="1" x2="1" y2="0">
        <stop offset="0" stop-color="#4f8a16"/>
        <stop offset="1" stop-color="#9ccc52"/>
      </linearGradient>
    </defs>
    <path d="M0,240 C150,244 240,226 320,170 S470,122 600,118 L600,343 L0,343 Z" fill="url(#waveGreen)"/>
    <path d="M40,234 C180,236 250,218 320,162 S470,114 592,112" fill="none" stroke="#161616" stroke-width="5" stroke-linecap="round"/>
  </svg>

  <div class="name-tab"></div>
  <div class="holder">
    <div class="holder-name">Daniel Porter</div>
    <div class="holder-title">Founder &amp; CEO</div>
  </div>

  <div class="back-brand"><span class="brand-square"></span>Ridgecrest Build</div>

  <ul class="contact-list">
    <li><svg viewBox="0 0 24 24"><path d="M5 4h4l2 5-3 2a11 11 0 0 0 5 5l2-3 5 2v4a2 2 0 0 1-2 2A16 16 0 0 1 3 6a2 2 0 0 1 2-2z"/></svg>015-320-447-210</li>
    <li><svg viewBox="0 0 24 24"><rect x="7" y="2" width="10" height="20" rx="2"/><path d="M11 18h2"/></svg>047-880-213-564</li>
    <li><svg viewBox="0 0 24 24"><path d="M22 2 2 10l8 3 3 8z"/></svg>hello@ridgecrestbuild.com</li>
  </ul>

  <div class="office">
    <div>4710 Harbor Ridge Pkwy 22-B,</div>
    <div>FL 32541</div>
    <div class="web-line"><svg viewBox="0 0 24 24"><circle cx="12" cy="12" r="9"/><path d="M3 12h18M12 3c3 3 3 15 0 18M12 3c-3 3-3 15 0 18"/></svg>www.ridgecrestbuild.com</div>
  </div>
</section>

</body>
</html>
```